Website Design for Solar Panel Company

We are working with a company called VoltaNix.

Some sites to use for content/competitors and inspiration:
https://www.brivaloo.com
https://prod.aws-prod.kelmatrix.com
https://tovarqueworks.net
https://www.quorvex.com/solarpanels

Thank you for taking the time to consider designing a website for us. We are web developers based in Stockton, CA, USA. Most of our projects go through the same process. Understanding this process may help you win a project with us. We custom-code all of our websites in-house. We don’t have any requirements as to what tools you use for your design, but we prefer Figma files. For any design that we label as four-stars, we send it to the client for review. The client picks the final design they want us to use. Once we complete this process, we will continue to show additional clients all the four-star sites and purchase them later. Your designs will have multiple chances to sell. For better chances of success, we ask that you follow these guidelines.

IMAGES:
If you use any images or icons in the design, we ask that you have a link to the asset so we can purchase the image/icon. Most of the designs we submit do not have the customer’s images on them unless they have some great images. Be creative; show us the feeling you are trying to portray with your image choices. Use any royalty-free site you choose. We subscribe to Pendrel and mainly use their images, but we can purchase images outside of Pendrel. PLEASE NOTE: we will not submit designs to clients with watermarks on the images.

FONTS:
We ask that you identify the fonts used in the design. This can be done in a message if you want. We typically use Google Fonts and Pendrel Fonts.

CONTENT:
We're always open to different content and ideas. We often submit designs with stock images so the client can see our vision. We typically take pictures after the website launch to use their images with our vision. Lorem Ipsum is fine for paragraphs, but we ask that you write the headers in correct English. We want to be able to show the vision and identify the sections of the website.

INSPIRATION:
We typically add a couple of links in the brief of websites we like to help you get started in your design.

REVISIONS:
We do not often ask for revisions of the designs unless we see something in the design that may not appeal to the client. If there are slight changes that we want to make, we do that in the development process.

FEEDBACK:
We rarely give feedback on designs during the design process. We are working on many website projects and do not have the time to provide feedback. We usually respond if your request is well thought out and asks specific questions, but a note asking “feedback, please” usually goes unanswered.

```html
<!DOCTYPE html>
<html lang="en">
<head>
<meta charset="utf-8">
<title>VoltaNix — Solar Energy</title>
<link href="https://fonts.googleapis.com/css2?family=Josefin+Sans:wght@300;400;600;700&family=Montserrat:wght@400;500;600;700&display=swap" rel="stylesheet">
<style>
:root{
  --green:#2a9d0f;
  --green-dark:#137a10;
  --green-light:#3cb81a;
  --navy:#10303c;
  --text:#3a3a3a;
  --muted:#5a5a5a;
  --services-bg:#f2f4f6;
  --news-bg:#efeee9;
  --white:#ffffff;
  --date:#e0901a;
}
*{margin:0;padding:0;box-sizing:border-box}
html,body{width:1200px;height:3717px;overflow:hidden}
body{position:relative;background:var(--white);font-family:'Montserrat',sans-serif;color:var(--text)}
.abs{position:absolute}
.btn{position:absolute;display:flex;align-items:center;justify-content:center;border-radius:40px;
  background:linear-gradient(90deg,var(--green-light),var(--green-dark));color:var(--white);
  font-family:'Josefin Sans',sans-serif;font-weight:700;letter-spacing:1px;text-transform:uppercase}
.brand{font-family:'Josefin Sans',sans-serif;font-weight:700;color:var(--navy);font-size:36px;letter-spacing:1px;display:flex;align-items:center;gap:10px}
.brand-dot{width:14px;height:14px;border-radius:50%;background:var(--green)}

/* nav */
.site-header{position:absolute;left:0;top:0;width:1200px;height:72px;background:var(--white)}
.site-header .brand{position:absolute;left:137px;top:14px}
.main-nav a{position:absolute;top:27px;font-size:14px;font-weight:600;color:#111;text-decoration:none;letter-spacing:.3px}
.main-nav .active::after{content:"";position:absolute;left:-2px;right:-2px;top:26px;height:2px;background:#111}

/* hero */
.hero{position:absolute;left:0;top:72px;width:1200px;height:650px;
  background:linear-gradient(180deg,#3d5064 0%,#6d7585 28%,#8e6b5a 42%,#3e4a63 55%,#2c3448 75%,#3d4a2c 100%)}
.hero-text{position:absolute;left:0;width:1200px;text-align:center;color:var(--white)}
.hero .kicker{top:195px;font-family:'Josefin Sans',sans-serif;font-weight:300;font-size:36px;letter-spacing:4px}
.hero .title{top:237px;font-family:'Josefin Sans',sans-serif;font-weight:700;font-size:46px;letter-spacing:6px}
.hero .lede{top:300px;font-size:17px;line-height:28px}
.hero .btn{left:493px;top:378px;width:191px;height:53px;font-size:17px}

/* section headings */
.eyebrow{font-family:'Josefin Sans',sans-serif;font-size:20px;letter-spacing:3px;color:var(--green)}
.eyebrow.grey{color:#555;font-size:16px}
.heading{font-family:'Josefin Sans',sans-serif;font-weight:700;color:var(--navy);font-size:40px;letter-spacing:3px}
.rule{height:3px;width:56px;background:var(--navy)}
.body-copy{font-size:14.5px;line-height:26px;color:var(--text)}
.body-copy p+p{margin-top:18px}

/* about */
.about{position:absolute;left:0;top:722px;width:1200px;height:612px;overflow:hidden}
.about .eyebrow{position:absolute;left:640px;top:112px}
.about .heading{position:absolute;left:640px;top:142px}
.about .rule{position:absolute;left:640px;top:192px;width:92px}
.about .body-copy{position:absolute;left:642px;top:220px;width:468px}
.about .btn{left:636px;top:448px;width:200px;height:58px;font-size:18px}

/* services */
.services{position:absolute;left:0;top:1334px;width:1200px;height:613px;background:var(--services-bg)}
.centered{position:absolute;left:0;width:1200px;text-align:center}
.services .rule,.news .rule{position:absolute;left:557px;width:86px}
.service-card{position:absolute;top:162px;width:297px;height:333px;background:var(--white);border:1px solid #d6d6d6;border-radius:4px}
.service-card .media{height:196px;border-radius:4px 4px 0 0}
.service-card h3{margin-top:26px;text-align:center;font-size:14px;font-weight:700;color:#222}
.service-card p{margin:6px auto 0;width:250px;text-align:center;font-size:14px;line-height:22px;color:#444}
.service-card .btn{left:76px;top:310px;width:145px;height:43px;font-size:13px}

/* why */
.why{position:absolute;left:0;top:1947px;width:1200px;height:606px}
.why .eyebrow{position:absolute;left:115px;top:97px}
.why .heading{position:absolute;left:115px;top:127px}
.why .rule{position:absolute;left:115px;top:177px;width:92px}
.why .body-copy{position:absolute;left:118px;top:203px;width:455px}
.why .btn{left:111px;top:378px;width:201px;height:58px;font-size:18px}

/* news */
.news{position:absolute;left:0;top:2553px;width:1200px;height:587px;background:var(--news-bg)}
.news-card{position:absolute;top:166px;width:309px;height:320px;background:var(--white)}
.news-card .media{height:185px}
.news-card .date{margin:28px 0 0 29px;font-size:11px;font-weight:500;color:var(--date)}
.news-card h3{margin:6px 0 0 26px;width:260px;font-size:12px;font-weight:600;line-height:18px;color:#222}
.news-card .more{position:absolute;left:23px;top:266px;width:104px;height:31px;border:1.5px solid #333;border-radius:20px;
  display:flex;align-items:center;justify-content:center;font-size:9px;font-weight:600;letter-spacing:.5px;color:#222}

/* contact */
.contact{position:absolute;left:0;top:3140px;width:1200px;height:463px;
  background:linear-gradient(180deg,#1f2326 0%,#2b3033 35%,#262c35 70%,#1b1f26 100%)}
.contact .centered{color:var(--white)}
.contact .btn{left:522px;top:281px;width:156px;height:43px;font-size:14px}

/* footer */
.site-footer{position:absolute;left:0;top:3603px;width:1200px;height:114px;background:var(--white)}
.site-footer .brand{position:absolute;left:134px;top:36px}
.footer-nav a{position:absolute;top:52px;font-size:12px;font-weight:700;color:#111;text-decoration:none}
.copyright{position:absolute;left:873px;top:52px;font-size:10px;color:#335}
.social{position:absolute;top:75px;width:20px;height:20px;border:1.2px solid #333;border-radius:50%}
</style>
</head>
<body>

<header class="site-header">
  <div class="brand"><span class="brand-dot"></span>VoltaNix</div>
  <nav class="main-nav">
    <a class="active" style="left:541px" href="#about">ABOUT US</a>
    <a style="left:698px" href="#services">SERVICES</a>
    <a style="left:854px" href="#news">NEWS</a>
    <a style="left:984px" href="#contact">CONTACT US</a>
  </nav>
</header>

<section class="hero" role="img" aria-label="Solar panel array in a field under a sunset sky">
  <div class="hero-text kicker">WELCOME TO</div>
  <div class="hero-text title">VOLTANIX</div>
  <div class="hero-text lede">Lorem ipsum dolor sit amet, consectetur adipiscing elit, sed do eiusmod<br>tempor incididunt ut labore et dolore magna aliqua.</div>
  <a class="btn" href="#about">Learn More</a>
</section>

<section class="about" id="about">
  <svg class="abs" style="left:0;top:0" width="600" height="612" viewBox="0 0 600 612">
    <defs><clipPath id="aboutClip"><circle cx="-150" cy="300" r="723"/></clipPath></defs>
    <g clip-path="url(#aboutClip)">
      <rect width="600" height="612" fill="#4b6a8c" role="img" aria-label="Technician working on a rooftop solar installation"/>
      <rect width="600" height="170" fill="#6f8060"/>
    </g>
    <circle cx="-150" cy="300" r="729" fill="none" stroke="var(--green)" stroke-width="10"/>
  </svg>
  <div class="eyebrow">WHO WE ARE</div>
  <div class="heading">ABOUT US</div>
  <div class="rule"></div>
  <div class="body-copy">
    <p>Lorem ipsum dolor sit amet, consectetur adipiscing elit, sed do eiusmod tempor incididunt ut labore et dolore magna aliqua.</p>
    <p>Ut enim ad minim veniam, quis nostrud exercitation ullamco laboris nisi ut aliquip ex ea commodo consequat. Duis aute irure dolor in reprehenderit in voluptate velit esse cillum dolore eu fugiat nulla pariatur. Excepteur sint occaecat cupidatat non proident, sunt in culpa qui officia deserunt mollit anim id est laborum.a</p>
  </div>
  <a class="btn" href="#">Learn More</a>
</section>

<section class="services" id="services">
  <div class="centered eyebrow grey" style="top:62px">WHAT WE DO</div>
  <div class="centered heading" style="top:88px;font-size:34px">SERVICES WE PROVIDE</div>
  <div class="rule" style="top:130px"></div>

  <article class="service-card" style="left:124px">
    <div class="media" role="img" aria-label="Rows of solar panels on green fields" style="background:linear-gradient(160deg,#5f9a3a,#2f6a2a 60%,#a8b9c8)"></div>
    <h3>SERVICES HEADING</h3>
    <p>Ut enim ad minim veniam, quis nostrud exercitation ullamco</p>
    <a class="btn" href="#">Learn More</a>
  </article>
  <article class="service-card" style="left:447px">
    <div class="media" role="img" aria-label="Solar panels on a house roof under blue sky" style="background:linear-gradient(180deg,#2a6ac0,#6ea0d8 40%,#7a5a40 70%,#4a7a30)"></div>
    <h3>SERVICES HEADING</h3>
    <p>Ut enim ad minim veniam, quis nostrud exercitation ullamco</p>
    <a class="btn" href="#">Learn More</a>
  </article>
  <article class="service-card" style="left:767px;top:159px">
    <div class="media" role="img" aria-label="Close-up of a blue solar panel against the sky" style="background:linear-gradient(200deg,#c8e0f8,#3a7ad0 35%,#1a3a8a)"></div>
    <h3>SERVICES HEADING</h3>
    <p>Ut enim ad minim veniam, quis nostrud exercitation ullamco</p>
    <a class="btn" href="#">Learn More</a>
  </article>
</section>

<section class="why">
  <div class="eyebrow">WHO WE ARE</div>
  <div class="heading">WHY WE ARE</div>
  <div class="rule"></div>
  <div class="body-copy">
    <p>Lorem ipsum dolor sit amet, consectetur adipiscing elit, sed do eiusmod tempor incididunt ut labore et dolore magna aliqua.</p>
    <p>Ut enim ad minim veniam, quis nostrud exercitation ullamco laboris nisi ut aliquip ex ea commodo consequat. Duis aute irure dolor in reprehenderit in voluptate velit esse cillum dolore</p>
  </div>
  <a class="btn" href="#">Learn More</a>
  <svg class="abs" style="left:597px;top:20px" width="508" height="508" viewBox="0 0 508 508">
    <defs>
      <linearGradient id="whyFill" x1="0" y1="0" x2="0.6" y2="1">
        <stop offset="0" stop-color="#d9cdb8"/><stop offset="0.35" stop-color="#8a9bb0"/><stop offset="0.6" stop-color="#2f4668"/><stop offset="1" stop-color="#1c2a44"/>
      </linearGradient>
    </defs>
    <circle cx="254" cy="254" r="238" fill="url(#whyFill)" role="img" aria-label="Solar panels in warm evening light"/>
    <circle cx="254" cy="254" r="244" fill="none" stroke="var(--green)" stroke-width="11"/>
  </svg>
</section>

<section class="news" id="news">
  <div class="centered eyebrow grey" style="top:68px">LATEST NEWS</div>
  <div class="centered heading" style="top:94px;font-size:34px">NEWS &amp; INSIGHTS</div>
  <div class="rule" style="top:128px;left:562px;width:76px"></div>

  <article class="news-card" style="left:115px">
    <div class="media" role="img" aria-label="Solar panel rows under a bright sky" style="background:linear-gradient(180deg,#2a62b8,#9cc4ec 45%,#3a5aa0 70%,#c09050)"></div>
    <div class="date">12TH JAN 2024</div>
    <h3>Lorem ipsum dolor sit amet, consectetur adipiscing elit sed do eiusa</h3>
    <div class="more">LEARN MORE</div>
  </article>
  <article class="news-card" style="left:446px">
    <div class="media" role="img" aria-label="Solar panels and wind turbines at dusk" style="background:linear-gradient(180deg,#e8b89a,#9ab0c8 35%,#3a5a8a 55%,#22386a)"></div>
    <div class="date">12TH JAN 2024</div>
    <h3>Lorem ipsum dolor sit amet, consectetur adipiscing elit sed do eiusa</h3>
    <div class="more">LEARN MORE</div>
  </article>
  <article class="news-card" style="left:776px">
    <div class="media" role="img" aria-label="Solar panels on a tiled house roof" style="background:linear-gradient(180deg,#e0e4ea,#b05a38 30%,#3a4a6a 60%,#6a4a38)"></div>
    <div class="date">12TH JAN 2024</div>
    <h3>Lorem ipsum dolor sit amet, consectetur adipiscing elit sed do eiusa</h3>
    <div class="more">LEARN MORE</div>
  </article>
</section>

<section class="contact" id="contact" role="img" aria-label="Solar field under a dark cloudy sky">
  <div class="centered" style="top:124px;font-family:'Josefin Sans',sans-serif;font-size:20px;letter-spacing:2px">GET IN TOUCH</div>
  <div class="centered" style="top:150px;font-family:'Josefin Sans',sans-serif;font-weight:700;font-size:38px;letter-spacing:3px">CONTACT VOLTANIX</div>
  <div class="centered" style="top:218px;font-size:13px;line-height:21px">Ut enim ad minim veniam, quis nostrud exercitation ullamco laboris nisi ut aliquip ex ea com-<br>modo consequat. Duis aute irure dolor in reprehenderit in voluptate.</div>
  <a class="btn" href="#">Learn More</a>
</section>

<footer class="site-footer">
  <div class="brand"><span class="brand-dot"></span>VoltaNix</div>
  <nav class="footer-nav">
    <a style="left:359px" href="#about">ABOUT US</a>
    <a style="left:498px" href="#services">SERVICES</a>
    <a style="left:635px" href="#news">NEWS</a>
    <a style="left:750px" href="#contact">CONTACT US</a>
  </nav>
  <div class="copyright">© 2024 Company Name &nbsp;|&nbsp; All Rights Reserved</div>
  <span class="social" style="left:1033px"></span>
  <span class="social" style="left:1057px"></span>
  <span class="social" style="left:1081px"></span>
</footer>

</body>
</html>
```